website design for M&T Electric

A portfolio website for a high end commercial and residential electrical contracting company. The current site mandtelectric.example does not represent the current direction but the images in the gallery give you an idea of the work we do. Current logo will be uploaded shortly but is black text on white background.
Target Market(s)
General Contractors, Residential Home Owners, clients intersted in Velmora home automation.
Industry/Entity Type
Electrician
Coding
Coded - Design and coding required
Number of Pages Required
2 page
Font styles to use
Sans Serif
Colors
Designer to choose colors to be used in the design.
Requirements
Must have
- Portfolio section highlighting different service areas and products (Velmora Housepilot, etc)

```html
<!DOCTYPE html>
<html lang="en">
<head>
<meta charset="utf-8">
<title>M&amp;T Electric</title>
<link href="https://fonts.googleapis.com/css2?family=Open+Sans:wght@400;600;700;800&display=swap" rel="stylesheet">
<style>
:root{
  --blue:#1a86c1;
  --black:#080808;
  --dark:#111;
  --ink:#222;
  --muted:#555;
  --light:#efefef;
  --white:#fff;
}
*{margin:0;padding:0;box-sizing:border-box}
html,body{width:1200px;height:2347px;overflow:hidden}
body{position:relative;font-family:"Open Sans",Arial,sans-serif;color:var(--ink);background:var(--white)}
.abs{position:absolute}
.site-header{left:0;top:0;width:1200px;height:91px;background:var(--black)}
.brand{left:131px;top:22px;font-size:36px;color:var(--white);font-weight:400;letter-spacing:-.5px}
.nav a{position:absolute;top:0;height:91px;line-height:91px;color:var(--white);font-size:14px;font-weight:600;text-decoration:none}
.nav .active{background:var(--blue);width:81px;text-align:center}
.hero{left:0;top:91px;width:1200px;height:504px;background:linear-gradient(120deg,#3b5670 0%,#23364a 30%,#5d1f1a 55%,#1f4f86 75%,#33495c 100%)}
.hero-box{left:131px;top:235px;width:503px;height:156px;background:rgba(0,0,0,.72)}
.hero-title{left:157px;top:246px;font-size:34px;font-weight:800;color:var(--white);letter-spacing:.5px}
.hero-rule{left:157px;top:303px;width:470px;height:3px;background:linear-gradient(90deg,#c7a64a,#e7e7e7 60%,transparent)}
.hero-text{left:161px;top:322px;width:450px;font-size:14px;line-height:28px;color:#eee}
.btn{background:var(--blue);color:var(--white);font-weight:700;text-align:center;font-size:13px}
.hero-btn{left:131px;top:397px;width:141px;height:40px;line-height:40px}
.round-arrow{border-radius:50%;display:flex;align-items:center;justify-content:center}
.hero-arrow{width:32px;height:32px;background:rgba(255,255,255,.85)}
.services{left:0;top:595px;width:1200px;height:497px;background:var(--light)}
.section-title{width:1200px;text-align:center;font-size:28px;font-weight:700;color:var(--ink)}
.section-lead{width:1200px;text-align:center;font-size:12px;line-height:20px;color:#444}
.card{top:810px;width:291px;height:210px;background:var(--white);border:1px solid #ddd;text-align:center}
.card.featured{background:var(--blue);border-color:var(--blue);color:var(--white)}
.card h3{margin-top:54px;font-size:14px;font-weight:700}
.card p{margin:8px auto 0;width:240px;font-size:12px;line-height:20px;color:#555}
.card.featured p{color:var(--white)}
.card .view{position:absolute;left:96px;top:152px;width:98px;height:36px;line-height:36px;font-size:11px;font-weight:700;background:var(--blue);color:var(--white)}
.card.featured .view{background:var(--white);color:var(--blue)}
.card-icon{width:90px;height:90px;top:761px;border-radius:50%;background:var(--white);border:1px solid #ddd;display:flex;align-items:center;justify-content:center}
.card-icon.featured{background:var(--blue);border:3px solid var(--white)}
.side-arrow{width:40px;height:40px;background:#d2d2d2;top:895px}
.welcome-kicker{left:131px;top:1154px;font-size:21px}
.welcome-title{left:131px;top:1184px;font-size:28px;font-weight:700}
.welcome-text{left:131px;top:1232px;width:430px;font-size:12px;line-height:23px;color:#444}
.bullets{left:131px;top:1320px;list-style:none;font-size:12px;color:#333}
.bullets li{height:36px;display:flex;align-items:flex-start;gap:10px}
.bullets .dot{width:14px;height:14px;border-radius:50%;background:var(--blue);display:flex;align-items:center;justify-content:center;margin-top:2px}
.welcome-btn{left:131px;top:1443px;width:141px;height:39px;line-height:39px}
.photo{overflow:hidden}
.photo .frame{position:absolute;inset:8px;border:1px solid rgba(255,255,255,.8)}
.feature-title{left:851px;font-size:14px;font-weight:600;color:var(--blue);letter-spacing:.3px}
.feature-text{left:851px;width:230px;font-size:12px;line-height:23px;color:#444}
.feature-link{left:851px;font-size:10px;font-weight:700;color:var(--blue)}
.gallery{left:0;top:1555px;width:1200px;height:501px;background:linear-gradient(180deg,#121212,#0a0a0a)}
.gallery .section-title,.gallery .section-lead{color:var(--white)}
.tab{top:1700px;height:41px;line-height:39px;border:1px solid #777;color:var(--white);font-size:15px;font-weight:600;text-align:center}
.tab.active{background:var(--blue);border-color:#7cc0e4}
.gallery-panel{left:133px;top:1741px;width:934px;height:237px;border:1px solid #444}
.footer{left:0;top:2056px;width:1200px;height:291px;background:var(--light)}
.footer h4{position:absolute;top:2094px;font-size:15px;font-weight:600;color:var(--blue)}
.footer-links{left:131px;top:2132px;list-style:none;font-size:11px;color:#333}
.footer-links li{height:24px}
.news-text{left:318px;top:2132px;width:270px;font-size:11px;line-height:24px;color:#333}
.news-input{left:318px;top:2187px;width:250px;height:36px;border:1px solid #ccc;background:var(--white);font-size:11px;color:#555;padding:10px 14px}
.news-btn{left:321px;top:2230px;width:81px;height:34px;line-height:34px;font-size:10px;border-radius:2px}
.contact-row{left:681px;display:flex;gap:14px;font-size:11px;color:#333;line-height:16px}
.contact-row svg{flex:none;margin-top:1px}
.follow-row{left:970px;display:flex;align-items:center;gap:12px;font-size:11px;color:#333}
.follow-row .ring{width:32px;height:32px;border:1px solid #888;border-radius:50%}
.footer-rule{left:133px;top:2298px;width:937px;height:1px;background:#bbb}
.copyright{left:0;top:2314px;width:1200px;text-align:center;font-size:11px;color:#444}
</style>
</head>
<body>

<header class="abs site-header">
  <div class="abs brand">M&amp;T Electric</div>
  <nav class="nav">
    <a class="active" style="left:474px">HOME</a>
    <a style="left:581px">GALLERY</a>
    <a style="left:682px">SPECIALTY SERVICES</a>
    <a style="left:852px">ABOUT</a>
    <a style="left:943px">CONTACT</a>
    <a style="left:1055px;top:38px;height:auto;line-height:1"><svg width="14" height="14" viewBox="0 0 14 14"><circle cx="6" cy="6" r="4.2" fill="none" stroke="#fff" stroke-width="2"/><line x1="9" y1="9" x2="13" y2="13" stroke="#fff" stroke-width="2"/></svg></a>
  </nav>
</header>

<section>
  <div class="abs hero" role="img" aria-label="Close-up photo of cut multicoloured electrical cables"></div>
  <div class="abs hero-box"></div>
  <h1 class="abs hero-title">ELECTRICAL CONTRACTING</h1>
  <div class="abs hero-rule"></div>
  <p class="abs hero-text">Lorem ipsum dolor sit amet, consectetur adipiscing elit, sed do eiusmod tempor incididunt ut labore et dolore magna aliqua...</p>
  <div class="abs btn hero-btn">LEARN MORE INFO</div>
  <div class="abs round-arrow hero-arrow" style="left:75px;top:294px"><svg width="12" height="14" viewBox="0 0 12 14"><path d="M8 2 3 7l5 5" fill="none" stroke="#333" stroke-width="2.5"/></svg></div>
  <div class="abs round-arrow hero-arrow" style="left:1092px;top:294px"><svg width="12" height="14" viewBox="0 0 12 14"><path d="M4 2l5 5-5 5" fill="none" stroke="#333" stroke-width="2.5"/></svg></div>
</section>

<section>
  <div class="abs services"></div>
  <h2 class="abs section-title" style="left:0;top:650px">OUR SERVICES</h2>
  <p class="abs section-lead" style="left:0;top:691px">Lorem ipsum dolor sit amet, consectetur adipiscing elit, sed do eiusmod tempor incididunt ut labore et dolore magna aliqua.<br>Ut enim ad minim veniam, quis nostrud exercitation ullamco laboris</p>

  <article class="abs card featured" style="left:133px">
    <h3>VELMORA HOUSEPILOT</h3>
    <p>We're proudly certified to install Velmora Housepilot systems. Housepilot gives you complete control over...</p>
    <div class="view">VIEW MORE ⊙</div>
  </article>
  <article class="abs card" style="left:454px">
    <h3>LED LIGHTING</h3>
    <p>LED Lighting has rapidly become a functional and affordable option. LED Lighting is a high efficiency energy saving...</p>
    <div class="view">VIEW MORE ⊙</div>
  </article>
  <article class="abs card" style="left:776px">
    <h3>EMERGENCY GENERATORS</h3>
    <p>Never be without power again--protect yourself from frozen pipes, inconvenience, and spoiled food. We sell, service...</p>
    <div class="view">VIEW MORE ⊙</div>
  </article>

  <div class="abs card-icon featured" style="left:233px">
    <svg width="50" height="46" viewBox="0 0 50 46"><path d="M25 3 3 22h6v21h12V31h8v12h12V22h6z" fill="#fff"/></svg>
  </div>
  <div class="abs card-icon" style="left:554px">
    <svg width="34" height="50" viewBox="0 0 34 50"><path d="M5 22a12 12 0 0 1 24 0v6H5z" fill="#1a86c1"/><rect x="2" y="29" width="30" height="5" fill="#1a86c1"/><rect x="11" y="34" width="3" height="14" fill="#1a86c1"/><rect x="20" y="34" width="3" height="12" fill="#1a86c1"/></svg>
  </div>
  <div class="abs card-icon" style="left:876px">
    <svg width="52" height="40" viewBox="0 0 52 40"><rect x="4" y="6" width="44" height="4" fill="#1a86c1"/><rect x="10" y="1" width="8" height="4" fill="#1a86c1"/><rect x="34" y="1" width="8" height="4" fill="#1a86c1"/><rect x="2" y="12" width="48" height="26" fill="#1a86c1"/><rect x="9" y="24" width="9" height="3" fill="#fff"/><path d="M26 16l-4 10h4l-2 8 6-11h-4l2-7z" fill="#fff"/><rect x="34" y="24" width="10" height="3" fill="#fff"/><rect x="37.5" y="20.5" width="3" height="10" fill="#fff"/></svg>
  </div>

  <div class="abs round-arrow side-arrow" style="left:108px"><svg width="10" height="12" viewBox="0 0 10 12"><path d="M7 1 2 6l5 5" fill="none" stroke="#fff" stroke-width="2"/></svg></div>
  <div class="abs round-arrow side-arrow" style="left:1052px"><svg width="10" height="12" viewBox="0 0 10 12"><path d="M3 1l5 5-5 5" fill="none" stroke="#fff" stroke-width="2"/></svg></div>
</section>

<section>
  <div class="abs welcome-kicker">WELCOME TO</div>
  <h2 class="abs welcome-title">MANDTELECTRIC</h2>
  <p class="abs welcome-text">Lorem ipsum dolor sit amet, consectetur adipiscing elit, sed do eiusmod tempor incididunt ut labore et dolore magna aliqua. Ut enim ad minim veniam, quis trud irure dolor in reprehenderit in voluptate velit esse...</p>
  <ul class="abs bullets">
    <li><span class="dot"><svg width="6" height="8" viewBox="0 0 6 8"><path d="M1 1l3 3-3 3" fill="none" stroke="#fff" stroke-width="1.6"/></svg></span>Lorem ipsum dolor sit amet, consectetur adipiscing elit, sed do eiusmode</li>
    <li><span class="dot"><svg width="6" height="8" viewBox="0 0 6 8"><path d="M1 1l3 3-3 3" fill="none" stroke="#fff" stroke-width="1.6"/></svg></span>Lorem ipsum dolor sit amet, consectetur adipiscing elit, sed do eiusmode</li>
    <li><span class="dot"><svg width="6" height="8" viewBox="0 0 6 8"><path d="M1 1l3 3-3 3" fill="none" stroke="#fff" stroke-width="1.6"/></svg></span>Lorem ipsum dolor sit amet, consectetur adipiscing elit, sed do eiusmode</li>
  </ul>
  <div class="abs btn welcome-btn">LEARN MORE INFO</div>

  <div class="abs photo" style="left:601px;top:1161px;width:220px;height:153px;background:linear-gradient(180deg,#3c66b8 0%,#8ea6cf 45%,#8c8172 65%,#5b5650 100%)" role="img" aria-label="Photo of a modern three-storey commercial building"><div class="frame"></div></div>
  <h3 class="abs feature-title" style="top:1176px">COMMERCIAL &nbsp;ELECTRICAL</h3>
  <p class="abs feature-text" style="top:1201px">Commodo consequat. Duis aute dolor in reprehenderit in voluptate velit dolore eu fugiat nulla pariatur....</p>
  <div class="abs feature-link" style="top:1283px">READ MORE INFO &#8250;</div>

  <div class="abs photo" style="left:601px;top:1330px;width:220px;height:153px;background:linear-gradient(135deg,#2a1a10 0%,#6b4424 40%,#a9763a 60%,#3a2414 100%)" role="img" aria-label="Photo of a wood-panelled home library interior"><div class="frame"></div></div>
  <h3 class="abs feature-title" style="top:1345px">RESIDENTIAL ELECTRICAL</h3>
  <p class="abs feature-text" style="top:1370px">Commodo consequat. Duis aute dolor in reprehenderit in voluptate velit dolore eu fugiat nulla pariatur....</p>
  <div class="abs feature-link" style="top:1452px">READ MORE INFO &#8250;</div>
</section>

<section>
  <div class="abs gallery" role="img" aria-label="Dark photo backdrop of a building at night"></div>
  <h2 class="abs section-title" style="left:0;top:1620px;color:#fff">GALLERY</h2>
  <p class="abs section-lead" style="left:0;top:1659px;color:#fff">Lorem ipsum dolor sit amet, consectetur adipiscing elit, sed do eiusmod tempor incididunt ut labore et dolore magna aliqua.</p>
  <div class="abs tab active" style="left:133px;width:124px">COMMERCIAL</div>
  <div class="abs tab" style="left:260px;width:125px">RESIDENTIAL</div>
  <div class="abs tab" style="left:388px;width:124px">LANDSCAPE</div>
  <div class="abs gallery-panel"></div>
  <div class="abs photo" style="left:149px;top:1763px;width:291px;height:193px;background:linear-gradient(180deg,#3a63b4 0%,#8da6d0 35%,#8a7058 60%,#4a5a3c 100%)" role="img" aria-label="Photo of a stone-clad commercial building with parked cars"><div class="frame"></div></div>
  <div class="abs photo" style="left:454px;top:1763px;width:291px;height:193px;background:linear-gradient(180deg,#dfe6ef 0%,#9b7a64 35%,#6e4a3a 65%,#8f8f8f 100%)" role="img" aria-label="Photo of a stone and brick residential complex"></div>
  <div class="abs photo" style="left:760px;top:1763px;width:291px;height:193px;background:linear-gradient(180deg,#3a63b4 0%,#90a8d0 45%,#8c8172 65%,#5b5650 100%)" role="img" aria-label="Photo of a modern three-storey commercial building"><div class="frame"></div></div>
</section>

<footer>
  <div class="abs footer"></div>
  <h4 style="left:131px">QUICK LINKS</h4>
  <ul class="abs footer-links">
    <li>Home</li><li>Gallery</li><li>Specialty Services</li><li>About</li><li>Contact</li>
  </ul>

  <h4 style="left:318px">NEWSLETTER</h4>
  <p class="abs news-text">Enter your email address to receive the latest news and notes from our blog.</p>
  <div class="abs news-input">Enter Your Mail Id</div>
  <div class="abs btn news-btn">SUBSCRIBE</div>

  <h4 style="left:681px">CONTACT INFO</h4>
  <div class="abs contact-row" style="top:2134px"><svg width="12" height="12" viewBox="0 0 12 12"><path d="M1 3c2-2 8-2 10 0v2H8V4H4v1H1z M2 6h8l1 5H1z" fill="#444"/></svg>(555) 014-2234</div>
  <div class="abs contact-row" style="top:2161px"><svg width="12" height="12" viewBox="0 0 12 12"><rect x="3" y="0" width="6" height="4" fill="#444"/><rect x="0" y="4" width="12" height="5" fill="#444"/><rect x="3" y="8" width="6" height="4" fill="#444" stroke="#fff" stroke-width=".8"/></svg>(555) 017-4100</div>
  <div class="abs contact-row" style="top:2189px"><svg width="12" height="10" viewBox="0 0 12 10"><rect x="0" y="1" width="12" height="8" fill="#444"/><path d="M0 1l6 4 6-4" fill="none" stroke="#fff" stroke-width="1"/></svg><span style="text-decoration:underline">jmorrow@mandtelectric.example</span></div>
  <div class="abs contact-row" style="top:2216px"><svg width="12" height="14" viewBox="0 0 12 14"><path d="M6 1a4 4 0 0 1 4 4c0 3-4 8-4 8S2 8 2 5a4 4 0 0 1 4-4z" fill="#444"/><circle cx="6" cy="5" r="1.5" fill="#fff"/></svg><span>#2150 Harbor Lane PO Box 4410<br>Westbrook, ID 83000</span></div>

  <h4 style="left:970px">FOLLOW US</h4>
  <div class="abs follow-row" style="top:2131px"><span class="ring"></span>Socialpage</div>
  <div class="abs follow-row" style="top:2170px"><span class="ring"></span>Chirper</div>
  <div class="abs follow-row" style="top:2209px"><span class="ring"></span>Circles Plus</div>

  <div class="abs footer-rule"></div>
  <p class="abs copyright">©2017 . M&amp;T Electric | All rights reserved</p>
</footer>

</body>
</html>
```